Pavecrest Works

Im looking for something similar to (tarvalepaving.com) web site. I really want it to pop!
services we offer:
- Seal Coating
- Crack Filling
- Striping
- Asphalt
- Concrete
- Signage
- Road Grinding
- Grading
- Hydro Blasting
- Recycled asphalt
- Dumpster Pads
- Pressure Washing
- Wheel blocks
- Bollard installation
- Commercial Curbing
- Job site clean up
- Sweeping
- Forestry Clean up
- ADA Compliant work
- Speed bump installation and removal
- Snow removal
- Custom stair sets (Commercial)
Target Market(s)
Parking lot maintenance, asphalt repairs, road grading
Industry/Entity Type
construction, parking lot maintenance
Number of Pages Required
2 page

```html
<!DOCTYPE html>
<html lang="en">
<head>
<meta charset="utf-8">
<title>Pavecrest Works – Home Page Light and Dark</title>
<link href="https://fonts.googleapis.com/css2?family=Poppins:wght@600;700&family=Roboto:wght@400;500;700&display=swap" rel="stylesheet">
<style>
:root{
  --green:#6cd400;
  --black:#000;
  --white:#fff;
  --board:#efefef;
}
*{box-sizing:border-box;margin:0;padding:0}
html,body{width:802px;height:1200px;overflow:hidden;background:var(--board)}
body{font-family:'Roboto',sans-serif}
.board{position:absolute;left:0;top:0;width:1568px;height:2347px;transform:scale(0.51148);transform-origin:0 0;background:var(--board)}

.page{
  --nav-bg:#fff;--about-bg:#fff;--soft:#f1fde6;--blog-bg:#fff;--card:#fff;
  --ink:#111;--muted:#7a7a7a;--field:#fff;--field-border:#dcdcdc;--field-text:#777;
  --shadow:0 2px 8px rgba(0,0,0,.12);
  position:absolute;top:72px;width:678px;height:2204px;overflow:hidden;background:var(--about-bg);color:var(--ink)
}
.page--light{left:74px}
.page--dark{
  left:816px;
  --nav-bg:#141414;--about-bg:#151515;--soft:#000;--blog-bg:#000;--card:#121212;
  --ink:#fff;--muted:#d6d6d6;--field:transparent;--field-border:#d0d0d0;--field-text:#fff;
  --shadow:none;
}
.section{position:absolute;left:0;width:678px}
.green{color:var(--green)}

/* top bar */
.topbar{top:0;height:26px;background:var(--black);color:var(--white);font-size:8.5px;font-weight:500}
.topbar__contact{position:absolute;left:63px;top:8px;display:flex;gap:6px;align-items:center}
.topbar__contact svg{width:8px;height:8px}
.topbar__social{position:absolute;right:0;top:0;width:162px;height:26px;background:var(--green);display:flex;justify-content:flex-end;gap:7px;align-items:center;padding-right:52px}
.topbar__social span{width:6px;height:6px;background:var(--black);border-radius:50%}

/* nav */
.nav{top:26px;height:45px;background:var(--nav-bg)}
.brand{position:absolute;left:63px;top:14px;font-family:'Poppins',sans-serif;font-weight:700;font-size:13px;letter-spacing:.5px;color:var(--ink);text-transform:uppercase}
.menu{position:absolute;right:63px;top:18px;display:flex;gap:13px;font-size:8px;font-weight:700;color:var(--ink)}
.menu .is-active{color:var(--green)}

/* hero */
.hero{top:71px;height:345px;background:var(--about-bg)}
.hero__photo{position:absolute;inset:0;background:linear-gradient(180deg,#8b8a85 0%,#9a9188 18%,#8f4b45 32%,#a25650 60%,#9b4b47 100%)}
.hero__title{position:absolute;top:88px;width:100%;text-align:center;font-family:'Poppins',sans-serif;font-weight:700;font-size:29px;color:var(--white)}
.hero__sub{position:absolute;top:129px;width:100%;text-align:center;font-size:9.5px;font-weight:700;color:var(--white)}
.hero__btn{position:absolute;top:156px;left:298px;width:82px;height:27px;border:2px solid var(--green);color:var(--white);font-size:8px;font-weight:700;display:flex;align-items:center;justify-content:center}
.hero__arrow{position:absolute;top:135px;width:21px;height:21px;border-radius:50%;background:var(--white);display:flex;align-items:center;justify-content:center}
.hero__arrow--prev{left:21px}.hero__arrow--next{right:22px}
.hero__cut{position:absolute;left:0;bottom:0;width:678px;height:90px}

/* about */
.about{top:416px;height:365px;background:var(--about-bg)}
.about__photo{position:absolute;left:63px;top:40px;width:324px;height:242px;background:linear-gradient(180deg,#c9cdd3 0%,#b7a67a 38%,#6f7a3f 55%,#5d4a37 80%,#4b3b2d 100%)}
.about__frame{position:absolute;left:387px;top:60px;width:227px;height:230px;border:3px solid var(--green);border-left:none}
.about__card{position:absolute;left:320px;top:79px;width:275px;height:232px;background:var(--card);box-shadow:var(--shadow);padding:20px 18px}
.page--dark .about__card{background:#000}
.h2{font-family:'Poppins',sans-serif;font-weight:700;font-size:21px;color:var(--ink)}
.about__card p{font-size:7.5px;line-height:14.5px;color:var(--muted);margin-top:10px;text-align:justify}
.btn-outline{display:inline-flex;align-items:center;justify-content:center;border:2px solid var(--ink);color:var(--green);font-size:8px;font-weight:700;height:26px}
.about__card .btn-outline{margin-top:16px;width:76px}

/* services */
.services{top:781px;height:403px;background:var(--soft)}
.section-title{position:absolute;top:30px;width:100%;text-align:center}
.service{position:absolute;top:86px;width:176px;height:212px;background:var(--card);box-shadow:var(--shadow);text-align:center}
.service__photo{height:117px}
.service h3{margin-top:12px;font-size:10.5px;font-weight:700;color:var(--ink)}
.service p{margin:6px 10px 0;font-size:7.5px;line-height:13.5px;color:var(--muted)}
.btn-solid{position:absolute;display:flex;align-items:center;justify-content:center;background:var(--green);color:var(--black);font-size:8px;font-weight:700}
.service .btn-solid{left:53px;bottom:-14px;width:70px;height:27px}
.services__all{position:absolute;left:285px;top:339px;width:107px}

/* estimates */
.estimates{top:1184px;height:140px;background:var(--green);text-align:center;color:var(--white)}
.estimates h2{margin-top:24px;font-family:'Poppins',sans-serif;font-weight:700;font-size:21px}
.estimates p{margin-top:6px;font-size:10px;font-weight:500}
.estimates a{position:absolute;left:298px;top:85px;width:83px;height:25px;background:var(--white);color:var(--green);font-size:8px;font-weight:700;display:flex;align-items:center;justify-content:center}

/* blog */
.blog{top:1324px;height:397px;background:var(--blog-bg)}
.post{position:absolute;background:var(--card);box-shadow:var(--shadow)}
.post--main{left:63px;top:100px;width:271px;height:243px}
.post--main .post__photo{position:absolute;left:4px;top:4px;width:263px;height:145px}
.post--side{left:344px;width:271px;height:113px}
.post--side .post__photo{position:absolute;left:4px;top:4px;width:100px;height:105px}
.post__date{position:absolute;font-size:6.5px;font-weight:500;color:var(--green);background:var(--card);border:1px solid var(--field-border);padding:3px 7px}
.post h3{position:absolute;font-size:9.5px;font-weight:700;line-height:15px;color:var(--ink);text-transform:uppercase}
.post p{position:absolute;font-size:7.5px;line-height:13px;color:var(--muted)}

/* contact */
.touch{top:1721px;height:259px;background:var(--soft)}
.touch .section-title{top:26px}
.field{position:absolute;height:26px;background:var(--field);border:1px solid var(--field-border);font-size:8px;color:var(--field-text);padding:8px 7px}
.touch .btn-solid{left:280px;top:207px;width:117px;height:29px;gap:5px}

/* footer */
.footer{top:1980px;height:224px;background:var(--black);color:var(--white);text-align:center}
.footer__cut{position:absolute;left:0;top:0;width:678px;height:90px}
.footer__brand{position:absolute;top:58px;width:100%;font-family:'Poppins',sans-serif;font-weight:700;font-size:18px;letter-spacing:.5px;color:var(--white);text-transform:uppercase}
.footer__menu{position:absolute;top:107px;width:100%;display:flex;justify-content:center;gap:15px;font-size:9.5px;font-weight:500}
.footer__contact{position:absolute;top:131px;width:100%;display:flex;justify-content:center;gap:8px;font-size:8px;font-weight:500;align-items:center}
.footer__contact svg{width:8px;height:8px}
.footer__social{position:absolute;top:158px;width:100%;display:flex;justify-content:center;gap:6px}
.footer__social span{width:20px;height:20px;border:1px solid var(--green)}
.footer__social span:first-child{background:var(--green)}
.footer__rule{position:absolute;left:63px;right:63px;top:195px;border-top:1px solid #333}
.footer__legal{position:absolute;left:63px;right:63px;top:206px;display:flex;justify-content:space-between;font-size:6.5px;color:#ddd}
</style>
</head>
<body>
<div class="board">

<!-- ===== light theme ===== -->
<div class="page page--light">
  <div class="section topbar">
    <div class="topbar__contact">
      <svg viewBox="0 0 10 10"><path d="M2 0.5l2 2-1 1.2c.6 1.3 1.6 2.3 2.9 2.9L7 5.6l2 2L7.8 9.5C4 9 1 6 .5 2.2z" fill="#6cd400"/></svg>
      <span>123 - 456 - 7890</span><span>|</span>
      <svg viewBox="0 0 10 10"><rect x="0" y="2" width="10" height="7" fill="#6cd400"/><path d="M0 2l5 4 5-4" stroke="#000" fill="none"/></svg>
      <span>info@pavecrestworks.com</span>
    </div>
    <div class="topbar__social"><span></span><span></span><span></span><span></span></div>
  </div>
  <header class="section nav">
    <div class="brand">Pavecrest Works</div>
    <nav class="menu"><span class="is-active">HOME</span><span>ABOUT US</span><span>OUR SERVICES</span><span>OUR PROJECTS</span><span>BLOG</span><span>CONTACT US</span></nav>
  </header>
  <section class="section hero">
    <div class="hero__photo" role="img" aria-label="Red brick paved entrance road with a work truck and crew in the distance"></div>
    <h1 class="hero__title">PAVECREST WORKS</h1>
    <p class="hero__sub">LOREM IPSUM DOLOR SIT AMET CONSECTETUR ADIPISCING ELIT SED DO EIUSA</p>
    <span class="hero__btn">GET STARTED</span>
    <span class="hero__arrow hero__arrow--prev"><svg width="8" height="8" viewBox="0 0 8 8"><path d="M5.5 1L2.5 4l3 3" stroke="#000" stroke-width="1.5" fill="none"/></svg></span>
    <span class="hero__arrow hero__arrow--next"><svg width="8" height="8" viewBox="0 0 8 8"><path d="M2.5 1l3 3-3 3" stroke="#000" stroke-width="1.5" fill="none"/></svg></span>
    <svg class="hero__cut" viewBox="0 0 678 90" preserveAspectRatio="none">
      <polygon points="0,82 339,4 678,82 678,90 339,18 0,90" fill="#6cd400"/>
      <polygon points="0,90 339,22 678,90" fill="var(--about-bg)"/>
    </svg>
  </section>
  <section class="section about">
    <div class="about__photo" role="img" aria-label="Compact track loader grading soil beside a cornfield"></div>
    <div class="about__frame"></div>
    <div class="about__card">
      <h2 class="h2">ABOUT <span class="green">US</span></h2>
      <p>Sed ut perspiciatis unde omnis iste natus error sit voluptatem acc usantium doloremque laudantium, totam rem aperiam, eaque ipsa quae ab illo inventore veritatis et quasi architecto beatae vitae dicta sunt explicab ipsa luptatem quia volua.</p>
      <p>Lorem ipsum dolor sit amet, consectetur adipiscing elit, sed do eiusmod tempor incididunt ut labore et dolore magna aliqua. Ut enim ad minim veniam quis nostruda.</p>
      <span class="btn-outline">LEARN MORE</span>
    </div>
  </section>
  <section class="section services">
    <h2 class="h2 section-title"><span class="green">OUR</span> SERVICES</h2>
    <article class="service" style="left:63px"><div class="service__photo" role="img" aria-label="Seal coating machine in a parking garage" style="background:linear-gradient(180deg,#cfd2d4,#8b8e88 45%,#2c2e2f)"></div><h3>Seal Coating</h3><p>Lorem ipsum dolor sit amet, consectetur a dipiscing elit, sed do eiusmod tempor incid idunt ut labore et dolorea.</p><span class="btn-solid">LEARN MORE</span></article>
    <article class="service" style="left:251px"><div class="service__photo" role="img" aria-label="Roller compactor on fresh asphalt" style="background:linear-gradient(180deg,#a9b6c4,#8f8e7e 45%,#34373a)"></div><h3>Crack Filling</h3><p>Lorem ipsum dolor sit amet, consectetur a dipiscing elit, sed do eiusmod tempor incid idunt ut labore et dolorea.</p><span class="btn-solid">LEARN MORE</span></article>
    <article class="service" style="left:438px"><div class="service__photo" role="img" aria-label="Yellow bollards along a building wall" style="background:linear-gradient(180deg,#9c9580,#7a7460 50%,#d4b120 62%,#3a3b3c)"></div><h3>Striping</h3><p>Lorem ipsum dolor sit amet, consectetur a dipiscing elit, sed do eiusmod tempor incid idunt ut labore et dolorea.</p><span class="btn-solid">LEARN MORE</span></article>
    <span class="btn-outline services__all">VIEW ALL SERVICES</span>
  </section>
  <section class="section estimates">
    <h2>FREE ESTIMATES</h2>
    <p>CONTACT US TODAY FOR A FREE ESTIMATE ON OUR SERVICES.</p>
    <a>CONTACT NOW</a>
  </section>
  <section class="section blog">
    <h2 class="h2 section-title" style="top:46px">LATEST <span class="green">BLOG</span></h2>
    <article class="post post--main">
      <div class="post__photo" role="img" aria-label="Track loader spreading gravel on a site" style="background:linear-gradient(180deg,#c5d3e0,#a89a7a 45%,#8a7d66)"></div>
      <span class="post__date" style="left:22px;top:143px">13 NOV 2021</span>
      <h3 style="left:22px;top:171px;width:240px">Lorem ipsum dolor sit amet, consec tet adipiscing elitm dolo</h3>
      <p style="left:22px;top:208px;width:245px">Sed ut perspiciatis unde omnis iste natus error sit volup tatem accusants iste natus erroque.</p>
    </article>
    <article class="post post--side" style="top:100px">
      <div class="post__photo" role="img" aria-label="Paved path through pine trees" style="background:linear-gradient(180deg,#d8e3ea,#3e5a3a 45%,#6c6c66)"></div>
      <span class="post__date" style="left:120px;top:14px">13 NOV 2021</span>
      <h3 style="left:120px;top:40px;width:140px">Lorem ipsum dolor sit am consec tetur adipi</h3>
      <p style="left:120px;top:78px;width:140px">Sed ut perspiciatis unde omnis iste na tus error sit volua.</p>
    </article>
    <article class="post post--side" style="top:229px">
      <div class="post__photo" role="img" aria-label="Red paved road stretching ahead" style="background:linear-gradient(180deg,#cfd8de,#8b4a45 30%,#a0524d)"></div>
      <span class="post__date" style="left:120px;top:14px">13 NOV 2021</span>
      <h3 style="left:120px;top:40px;width:140px">Lorem ipsum dolor sit am consec tetur adipi</h3>
      <p style="left:120px;top:78px;width:140px">Sed ut perspiciatis unde omnis iste na tus error sit volua.</p>
    </article>
  </section>
  <section class="section touch">
    <h2 class="h2 section-title">GET IN <span class="green">TOUCH</span></h2>
    <div class="field" style="left:118px;top:73px;width:218px">Full Name</div>
    <div class="field" style="left:341px;top:73px;width:219px">Phone Number</div>
    <div class="field" style="left:118px;top:107px;width:218px">Email Address</div>
    <div class="field" style="left:341px;top:107px;width:219px">Subject</div>
    <div class="field" style="left:118px;top:141px;width:442px;height:49px">Message...</div>
    <span class="btn-solid">CONTACT NOW <svg width="9" height="9" viewBox="0 0 10 10"><path d="M1 5l8-4-3 8-1-3z" stroke="#000" fill="none"/></svg></span>
  </section>
  <footer class="section footer">
    <svg class="footer__cut" viewBox="0 0 678 90" preserveAspectRatio="none">
      <polygon points="0,0 678,0 678,86 339,4 0,86" fill="var(--soft)"/>
      <polygon points="0,86 339,4 678,86 678,80 339,0 0,80" fill="#6cd400"/>
      <polygon points="0,90 339,14 678,90 678,86 339,10 0,86" fill="#fff"/>
      <polygon points="0,90 339,22 678,90 678,94 339,26 0,94" fill="#6cd400"/>
    </svg>
    <div class="footer__brand">Pavecrest Works</div>
    <nav class="footer__menu"><span>HOME</span><span>ABOUT US</span><span>OUR SERVICES</span><span>OUR PROJECTS</span><span>BLOG</span><span>CONTACT US</span></nav>
    <div class="footer__contact">
      <svg viewBox="0 0 10 10"><path d="M2 0.5l2 2-1 1.2c.6 1.3 1.6 2.3 2.9 2.9L7 5.6l2 2L7.8 9.5C4 9 1 6 .5 2.2z" fill="#6cd400"/></svg>
      <span>123 - 456 - 7890</span><span>|</span>
      <svg viewBox="0 0 10 10"><rect x="0" y="2" width="10" height="7" fill="#6cd400"/><path d="M0 2l5 4 5-4" stroke="#000" fill="none"/></svg>
      <span>info@pavecrestworks.com</span>
    </div>
    <div class="footer__social"><span></span><span></span><span></span><span></span></div>
    <div class="footer__rule"></div>
    <div class="footer__legal"><span>© 2021 <b>PAVECREST WORKS</b>. All Rights Reserved</span><span>Privacy Policy &nbsp;|&nbsp; Terms Of Use</span></div>
  </footer>
</div>

<!-- ===== dark theme ===== -->
<div class="page page--dark">
  <div class="section topbar">
    <div class="topbar__contact">
      <svg viewBox="0 0 10 10"><path d="M2 0.5l2 2-1 1.2c.6 1.3 1.6 2.3 2.9 2.9L7 5.6l2 2L7.8 9.5C4 9 1 6 .5 2.2z" fill="#6cd400"/></svg>
      <span>123 - 456 - 7890</span><span>|</span>
      <svg viewBox="0 0 10 10"><rect x="0" y="2" width="10" height="7" fill="#6cd400"/><path d="M0 2l5 4 5-4" stroke="#000" fill="none"/></svg>
      <span>info@pavecrestworks.com</span>
    </div>
    <div class="topbar__social"><span></span><span></span><span></span><span></span></div>
  </div>
  <header class="section nav">
    <div class="brand">Pavecrest Works</div>
    <nav class="menu"><span class="is-active">HOME</span><span>ABOUT US</span><span>OUR SERVICES</span><span>OUR PROJECTS</span><span>BLOG</span><span>CONTACT US</span></nav>
  </header>
  <section class="section hero">
    <div class="hero__photo" role="img" aria-label="Red brick paved entrance road with a work truck and crew in the distance"></div>
    <h1 class="hero__title">PAVECREST WORKS</h1>
    <p class="hero__sub">LOREM IPSUM DOLOR SIT AMET CONSECTETUR ADIPISCING ELIT SED DO EIUSA</p>
    <span class="hero__btn">GET STARTED</span>
    <span class="hero__arrow hero__arrow--prev"><svg width="8" height="8" viewBox="0 0 8 8"><path d="M5.5 1L2.5 4l3 3" stroke="#000" stroke-width="1.5" fill="none"/></svg></span>
    <span class="hero__arrow hero__arrow--next"><svg width="8" height="8" viewBox="0 0 8 8"><path d="M2.5 1l3 3-3 3" stroke="#000" stroke-width="1.5" fill="none"/></svg></span>
    <svg class="hero__cut" viewBox="0 0 678 90" preserveAspectRatio="none">
      <polygon points="0,82 339,4 678,82 678,90 339,18 0,90" fill="#6cd400"/>
      <polygon points="0,90 339,22 678,90" fill="var(--about-bg)"/>
    </svg>
  </section>
  <section class="section about">
    <div class="about__photo" role="img" aria-label="Compact track loader grading soil beside a cornfield"></div>
    <div class="about__frame"></div>
    <div class="about__card">
      <h2 class="h2">ABOUT <span class="green">US</span></h2>
      <p>Sed ut perspiciatis unde omnis iste natus error sit voluptatem acc usantium doloremque laudantium, totam rem aperiam, eaque ipsa quae ab illo inventore veritatis et quasi architecto beatae vitae dicta sunt explicab ipsa luptatem quia volua.</p>
      <p>Lorem ipsum dolor sit amet, consectetur adipiscing elit, sed do eiusmod tempor incididunt ut labore et dolore magna aliqua. Ut enim ad minim veniam quis nostruda.</p>
      <span class="btn-outline">LEARN MORE</span>
    </div>
  </section>
  <section class="section services">
    <h2 class="h2 section-title"><span class="green">OUR</span> SERVICES</h2>
    <article class="service" style="left:63px"><div class="service__photo" role="img" aria-label="Seal coating machine in a parking garage" style="background:linear-gradient(180deg,#cfd2d4,#8b8e88 45%,#2c2e2f)"></div><h3>Seal Coating</h3><p>Lorem ipsum dolor sit amet, consectetur a dipiscing elit, sed do eiusmod tempor incid idunt ut labore et dolorea.</p><span class="btn-solid">LEARN MORE</span></article>
    <article class="service" style="left:251px"><div class="service__photo" role="img" aria-label="Roller compactor on fresh asphalt" style="background:linear-gradient(180deg,#a9b6c4,#8f8e7e 45%,#34373a)"></div><h3>Crack Filling</h3><p>Lorem ipsum dolor sit amet, consectetur a dipiscing elit, sed do eiusmod tempor incid idunt ut labore et dolorea.</p><span class="btn-solid">LEARN MORE</span></article>
    <article class="service" style="left:438px"><div class="service__photo" role="img" aria-label="Yellow bollards along a building wall" style="background:linear-gradient(180deg,#9c9580,#7a7460 50%,#d4b120 62%,#3a3b3c)"></div><h3>Striping</h3><p>Lorem ipsum dolor sit amet, consectetur a dipiscing elit, sed do eiusmod tempor incid idunt ut labore et dolorea.</p><span class="btn-solid">LEARN MORE</span></article>
    <span class="btn-outline services__all">VIEW ALL SERVICES</span>
  </section>
  <section class="section estimates">
    <h2>FREE ESTIMATES</h2>
    <p>CONTACT US TODAY FOR A FREE ESTIMATE ON OUR SERVICES.</p>
    <a>CONTACT NOW</a>
  </section>
  <section class="section blog">
    <h2 class="h2 section-title" style="top:46px">LATEST <span class="green">BLOG</span></h2>
    <article class="post post--main">
      <div class="post__photo" role="img" aria-label="Track loader spreading gravel on a site" style="background:linear-gradient(180deg,#c5d3e0,#a89a7a 45%,#8a7d66)"></div>
      <span class="post__date" style="left:22px;top:143px">13 NOV 2021</span>
      <h3 style="left:22px;top:171px;width:240px">Lorem ipsum dolor sit amet, consec tet adipiscing elitm dolo</h3>
      <p style="left:22px;top:208px;width:245px">Sed ut perspiciatis unde omnis iste natus error sit volup tatem accusants iste natus erroque.</p>
    </article>
    <article class="post post--side" style="top:100px">
      <div class="post__photo" role="img" aria-label="Paved path through pine trees" style="background:linear-gradient(180deg,#d8e3ea,#3e5a3a 45%,#6c6c66)"></div>
      <span class="post__date" style="left:120px;top:14px">13 NOV 2021</span>
      <h3 style="left:120px;top:40px;width:140px">Lorem ipsum dolor sit am consec tetur adipi</h3>
      <p style="left:120px;top:78px;width:140px">Sed ut perspiciatis unde omnis iste na tus error sit volua.</p>
    </article>
    <article class="post post--side" style="top:229px">
      <div class="post__photo" role="img" aria-label="Red paved road stretching ahead" style="background:linear-gradient(180deg,#cfd8de,#8b4a45 30%,#a0524d)"></div>
      <span class="post__date" style="left:120px;top:14px">13 NOV 2021</span>
      <h3 style="left:120px;top:40px;width:140px">Lorem ipsum dolor sit am consec tetur adipi</h3>
      <p style="left:120px;top:78px;width:140px">Sed ut perspiciatis unde omnis iste na tus error sit volua.</p>
    </article>
  </section>
  <section class="section touch">
    <h2 class="h2 section-title">GET IN <span class="green">TOUCH</span></h2>
    <div class="field" style="left:118px;top:73px;width:218px">Full Name</div>
    <div class="field" style="left:341px;top:73px;width:219px">Phone Number</div>
    <div class="field" style="left:118px;top:107px;width:218px">Email Address</div>
    <div class="field" style="left:341px;top:107px;width:219px">Subject</div>
    <div class="field" style="left:118px;top:141px;width:442px;height:49px">Message...</div>
    <span class="btn-solid">CONTACT NOW <svg width="9" height="9" viewBox="0 0 10 10"><path d="M1 5l8-4-3 8-1-3z" stroke="#000" fill="none"/></svg></span>
  </section>
  <footer class="section footer">
    <svg class="footer__cut" viewBox="0 0 678 90" preserveAspectRatio="none">
      <polygon points="0,0 678,0 678,86 339,4 0,86" fill="var(--soft)"/>
      <polygon points="0,86 339,4 678,86 678,80 339,0 0,80" fill="#6cd400"/>
      <polygon points="0,90 339,14 678,90 678,86 339,10 0,86" fill="#000"/>
      <polygon points="0,90 339,22 678,90 678,94 339,26 0,94" fill="#6cd400"/>
    </svg>
    <div class="footer__brand">Pavecrest Works</div>
    <nav class="footer__menu"><span>HOME</span><span>ABOUT US</span><span>OUR SERVICES</span><span>OUR PROJECTS</span><span>BLOG</span><span>CONTACT US</span></nav>
    <div class="footer__contact">
      <svg viewBox="0 0 10 10"><path d="M2 0.5l2 2-1 1.2c.6 1.3 1.6 2.3 2.9 2.9L7 5.6l2 2L7.8 9.5C4 9 1 6 .5 2.2z" fill="#6cd400"/></svg>
      <span>123 - 456 - 7890</span><span>|</span>
      <svg viewBox="0 0 10 10"><rect x="0" y="2" width="10" height="7" fill="#6cd400"/><path d="M0 2l5 4 5-4" stroke="#000" fill="none"/></svg>
      <span>info@pavecrestworks.com</span>
    </div>
    <div class="footer__social"><span></span><span></span><span></span><span></span></div>
    <div class="footer__rule"></div>
    <div class="footer__legal"><span>© 2021 <b>PAVECREST WORKS</b>. All Rights Reserved</span><span>Privacy Policy &nbsp;|&nbsp; Terms Of Use</span></div>
  </footer>
</div>

</div>
</body>
</html>
```